Business card design for holistic health care clinic

We need a double-sided business card design for our holistic health care clinic that integrates our logo design and also its color scheme. My business is called Valmira. It is an integrative medicine clinic. You have already done the logo for me. Please ensure an elegant and upscale design that is not cluttered, but still has all the necessary information (please see below for details).

Target Market(s)

Wellness, fitness, rehabilitation for educated, well-traveled open-minded clients who are focused on natural, organic, balanced and preventive healthcare and lifestyle.

Industry/Entity Type

Medical

Contact Information for Business Card

Modern, clean.

Number of Pages Required

1 page

Font styles to use
Serif
Sans Serif

Colors

Designer to choose colors to be used in the design.

Requirements
Must have
• Logo on one side, all other information on the other side.
• Other information should include:
• Tobias Wrenfeld - DOE, CPT, LMT
• 4100 East Marrow Drive
• Austin, TX 78119
• 512 555 0148
• 818 555 0192
• info@ValmiraHealth.example
• t.wrenfeld@ValmiraHealth.example
Nice to have
• Darker background on front - but not totally black - shaded/dark gray.

```html
<!DOCTYPE html>
<html lang="en">
<head>
<meta charset="utf-8">
<title>Valmira Business Card</title>
<link rel="stylesheet" href="https://fonts.googleapis.com/css2?family=Source+Sans+3:wght@400;600;700&display=swap">
<style>
  :root {
    --stage: #000000;
    --panel-blue: #12739f;
    --brand-blue: #1b8fcf;
    --paper: #ffffff;
    --ink: #3a3a3a;
    --rule: #4aa3d8;
  }
  * { margin: 0; padding: 0; box-sizing: border-box; }
  html, body {
    width: 1200px; height: 900px; overflow: hidden;
    background: var(--stage);
    font-family: "Source Sans 3", sans-serif;
  }
  .canvas { position: relative; width: 1200px; height: 900px; }

  .card {
    position: absolute; top: 300px; width: 442px; height: 273px;
    background: var(--paper);
    overflow: hidden;
  }
  .card--info { left: 152px; }
  .card--brand { left: 622px; }

  .brand-panel {
    position: absolute; left: 0; top: 0; width: 233px; height: 100%;
    background: var(--panel-blue);
    color: var(--paper);
    text-align: center;
  }
  .brand-panel .brand-name {
    position: absolute; left: 0; right: 0; top: 116px;
    font-size: 42px; font-weight: 700; letter-spacing: 1px; line-height: 1;
  }
  .brand-panel .brand-tagline {
    position: absolute; left: 0; right: 0; top: 159px;
    font-size: 12.5px; font-weight: 600; line-height: 1;
  }

  .details {
    position: absolute; left: 254px; top: 48px; width: 182px;
    color: var(--ink);
  }
  .person-name {
    font-size: 18px; font-weight: 700; color: var(--brand-blue);
    letter-spacing: 0.3px; line-height: 1;
  }
  .person-credentials { font-size: 11.5px; margin-top: 5px; line-height: 1; }
  .rule { width: 152px; height: 1px; background: var(--rule); margin: 15px 0 14px; }
  .address { font-size: 11.5px; line-height: 16px; text-transform: uppercase; }
  .contact-list { list-style: none; }
  .contact-list li {
    display: flex; align-items: center; gap: 5px;
    font-size: 9.5px; line-height: 15px; letter-spacing: -0.3px;
    text-transform: uppercase; white-space: nowrap;
  }
  .contact-list svg { width: 9px; height: 9px; flex: none; fill: var(--brand-blue); }

  .card--brand { text-align: center; color: var(--brand-blue); }
  .card--brand .brand-name {
    position: absolute; left: 0; right: 0; top: 112px;
    font-size: 66px; font-weight: 700; letter-spacing: 2px; line-height: 1;
  }
  .card--brand .brand-tagline {
    position: absolute; left: 0; right: 0; top: 176px;
    font-size: 18px; font-weight: 600; line-height: 1;
  }
  .website {
    position: absolute; left: 0; right: 0; top: 227px;
    font-size: 14px; line-height: 1;
  }
</style>
</head>
<body>
<main class="canvas">
  <section class="card card--info">
    <div class="brand-panel">
      <div class="brand-name">VALMIRA</div>
      <div class="brand-tagline">Integrative Holistic Medicine</div>
    </div>
    <div class="details">
      <h1 class="person-name">TOBIAS WRENFELD</h1>
      <p class="person-credentials">DOE,CPT,LMT</p>
      <div class="rule"></div>
      <p class="address">4100 East Marrow Drive<br>Austin, TX 78119</p>
      <div class="rule"></div>
      <ul class="contact-list">
        <li><svg viewBox="0 0 10 10" aria-hidden="true"><path d="M2.5 0h5a1 1 0 0 1 1 1v8a1 1 0 0 1-1 1h-5a1 1 0 0 1-1-1V1a1 1 0 0 1 1-1zm.5 1.5v6h4v-6z"/></svg>512 555 0148</li>
        <li><svg viewBox="0 0 10 10" aria-hidden="true"><path d="M0 3.5C2-.5 8-.5 10 3.5L8 4.5 7 3H3L2 4.5zM2 5h6l1 4H1z"/></svg>818 555 0192</li>
        <li><svg viewBox="0 0 10 10" aria-hidden="true"><path d="M0 2h10v6H0zm1 1v.3l4 2.5 4-2.5V3z"/></svg>info@ValmiraHealth.example</li>
        <li><svg viewBox="0 0 10 10" aria-hidden="true"><path d="M0 2h10v6H0zm1 1v.3l4 2.5 4-2.5V3z"/></svg>t.wrenfeld@ValmiraHealth.example</li>
      </ul>
    </div>
  </section>

  <section class="card card--brand">
    <div class="brand-name">VALMIRA</div>
    <div class="brand-tagline">Integrative Holistic Medicine</div>
    <div class="website">www.ValmiraHealth.example</div>
  </section>
</main>
</body>
</html>
```